Company director needs a business card design

I am a semi-retired former senior finance executive who sits on a number of public and private company boards and do some consulting work. I work largely with emerging businesses but deal regularly with top end of town lawyers, bankers etc. I need a thoughtful but relatively conservative design which would also resonate with my younger client base. Some colour would be good. Information limited to name, address, office tel, mobile and email.

Finance

```html
<!DOCTYPE html>
<html lang="en">
<head>
<meta charset="utf-8">
<title>Martin Caldwell — Business Cards</title>
<link href="https://fonts.googleapis.com/css2?family=Cinzel:wght@400;700&display=swap" rel="stylesheet">
<style>
  :root {
    --backdrop: #1e1f23;
    --card: #121214;
    --silver-light: #f2f2f2;
    --silver-mid: #b9babd;
    --silver-dark: #7d7f83;
    --gold-light: #f6dc7a;
    --gold-mid: #d39a32;
    --gold-dark: #8a4f12;
  }
  * { margin: 0; padding: 0; box-sizing: border-box; }
  html, body {
    width: 1200px;
    height: 802px;
    overflow: hidden;
    background: var(--backdrop);
  }
  .canvas {
    position: relative;
    width: 1200px;
    height: 802px;
    display: flex;
    justify-content: center;
    align-items: center;
    gap: 70px;
  }
  .business-card {
    position: relative;
    width: 350px;
    height: 530px;
    background: var(--card);
    font-family: "Cinzel", serif;
  }
  .contact-block {
    position: absolute;
    top: 40px;
    left: 26px;
    font-size: 12.5px;
    line-height: 15px;
    letter-spacing: 0.2px;
  }
  .contact-block .address { margin-bottom: 12px; }
  .contact-block p { display: block; }
  .holder-name {
    position: absolute;
    right: 26px;
    bottom: 34px;
    font-size: 20px;
    font-weight: 700;
    letter-spacing: 0.5px;
  }
  .foil-silver .contact-block,
  .foil-silver .holder-name,
  .foil-gold .contact-block,
  .foil-gold .holder-name {
    -webkit-background-clip: text;
    background-clip: text;
    color: transparent;
  }
  .foil-silver .contact-block,
  .foil-silver .holder-name {
    background-image: linear-gradient(115deg, var(--silver-light) 0%, var(--silver-mid) 45%, var(--silver-dark) 75%, var(--silver-light) 100%);
  }
  .foil-gold .contact-block,
  .foil-gold .holder-name {
    background-image: linear-gradient(115deg, var(--gold-mid) 0%, var(--gold-light) 40%, var(--gold-mid) 65%, var(--gold-dark) 100%);
  }
</style>
</head>
<body>
  <main class="canvas">
    <article class="business-card foil-silver">
      <div class="contact-block">
        <div class="address">
          <p>18 Harbourview Lane,</p>
          <p>Mosman NSW 2088</p>
        </div>
        <p class="office-tel">02 9000 4821</p>
        <p class="mobile">0400 512 376</p>
        <p class="email">martin_caldwell@mail.net.au</p>
      </div>
      <h1 class="holder-name">Martin Caldwell</h1>
    </article>

    <article class="business-card foil-gold">
      <div class="contact-block">
        <div class="address">
          <p>18 Harbourview Lane,</p>
          <p>Mosman NSW 2088</p>
        </div>
        <p class="office-tel">02 9000 4821</p>
        <p class="mobile">0400 512 376</p>
        <p class="email">martin_caldwell@mail.net.au</p>
      </div>
      <h2 class="holder-name">Martin Caldwell</h2>
    </article>
  </main>
</body>
</html>
```